Computer Company needs a Business card design

We need a business card design for our business. We assist people to transition to the KVS (Kestrel Vantage Scheme). The Verandal Crown Office-owned kvs™ network is a brand new telecommunications network currently being rolled out across Australia, giving access to a reliable broadband connection. Our niche market will predominantly be domestic customers in the 50+ age bracket. The assistance that we provide is everything from arranging the equipment, arranging the plan and contract term, appointment times, final testing of the network and any tweaks that need to be made. We basically PM the transition from start to finish. The business card design should be minimalist, should communicate loyalty and stability, should be easy to read and clearly explain what we do. We have asked for front and back. However, the back of the card does not have to include much information at all. It could be just a small design, or a repeat of our phone number. Up to you. The attached file only says what is required on the card. It does not specify where to arrange the text, what fonts to use, etc etc. As much as we would like to give you more info, due to our very limited design ability, we are not really able to send you any rough, or otherwise, designs of what we are after. Hopefully the above description is enough for you.

```html
<!DOCTYPE html>
<html lang="en">
<head>
<meta charset="utf-8">
<title>Linkway Business Card – Front and Back</title>
<link rel="stylesheet" href="https://fonts.googleapis.com/css2?family=Open+Sans:wght@400;600;700;800&display=swap">
<style>
  :root {
    --backdrop: #a9a9ad;
    --card-black: #0b0b0c;
    --card-edge: #1d1d20;
    --pattern-a: #1a1a1c;
    --pattern-b: #0c0c0d;
    --brand-grey: #9a9a9e;
    --tagline-grey: #d8d8dc;
    --name-white: #ffffff;
    --title-white: #e6e6e6;
    --detail-grey: #8b8b90;
    --accent-blue: #2f8fe0;
  }
  * { margin: 0; padding: 0; box-sizing: border-box; }
  html, body {
    width: 1200px;
    height: 863px;
    overflow: hidden;
  }
  body {
    background: var(--backdrop);
    font-family: "Open Sans", Arial, sans-serif;
    position: relative;
  }
  .card {
    position: absolute;
    width: 560px;
    height: 320px;
    border-radius: 26px;
    background: var(--card-black);
    border: 1px solid var(--card-edge);
    box-shadow: 0 18px 30px rgba(0, 0, 0, 0.35);
    overflow: hidden;
  }
  .card--front { left: 420px; top: 60px; }
  .card--back  { left: 220px; top: 470px; }

  .card__pattern {
    position: absolute;
    inset: 0;
    background: radial-gradient(ellipse at 55% 45%, var(--pattern-a) 0%, var(--pattern-b) 75%);
  }

  .brand {
    position: absolute;
    left: 0;
    right: 0;
    text-align: center;
  }
  .card--front .brand { top: 110px; }
  .card--back .brand  { top: 66px; }

  .brand__name {
    display: inline-flex;
    align-items: center;
    gap: 12px;
    font-size: 46px;
    font-weight: 800;
    letter-spacing: 1px;
    line-height: 1;
    color: var(--brand-grey);
  }
  .brand__dot {
    width: 14px;
    height: 14px;
    border-radius: 50%;
    background: var(--accent-blue);
  }
  .brand__tagline {
    margin-top: 12px;
    font-size: 13px;
    font-weight: 700;
    letter-spacing: 6px;
    color: var(--tagline-grey);
  }

  .person {
    position: absolute;
    left: 222px;
    top: 186px;
  }
  .person__name {
    font-size: 19px;
    font-weight: 700;
    color: var(--name-white);
    line-height: 1.1;
  }
  .person__title {
    font-size: 12px;
    font-weight: 400;
    color: var(--title-white);
  }

  .contact {
    position: absolute;
    left: 40px;
    bottom: 40px;
    display: flex;
    gap: 26px;
    font-size: 13px;
    color: var(--detail-grey);
  }
  .contact__label {
    color: var(--accent-blue);
    font-weight: 600;
    margin-right: 4px;
  }
</style>
</head>
<body>

  <section class="card card--front" aria-label="Card front">
    <div class="card__pattern" role="img" aria-label="Faint repeating pattern of scattered digits across the black card"></div>
    <div class="brand">
      <div class="brand__name"><span class="brand__dot"></span>LINKWAY</div>
      <div class="brand__tagline">KVS SWITCH PARTNERS</div>
    </div>
  </section>

  <section class="card card--back" aria-label="Card back">
    <div class="card__pattern" role="img" aria-label="Faint repeating pattern of scattered digits across the black card"></div>
    <div class="brand">
      <div class="brand__name"><span class="brand__dot"></span>LINKWAY</div>
      <div class="brand__tagline">KVS SWITCH PARTNERS</div>
    </div>
    <div class="person">
      <div class="person__name">Hartley</div>
      <div class="person__title">President</div>
    </div>
    <div class="contact">
      <span class="contact__item"><span class="contact__label">Web:</span>www.linkwayswitch.com.au</span>
      <span class="contact__item"><span class="contact__label">Cell:</span>0412784390</span>
    </div>
  </section>

</body>
</html>
```